Buch-/eBook-Cover für Sachbuch gesucht
Zielgruppe
We're selfpublishing nonfiction books. Interested are adults - mostly man (age range: 25-50) - who want to learn more about leadership at their workplaces.
Aufgabenstellung
The design should be clean and simple, title easy to read, good color contrast (the cover has to stand out from an white background).

```html
<!DOCTYPE html>
<html lang="en">
<head>
<meta charset="utf-8">
<title>Leadership – Book Cover</title>
<link rel="stylesheet" href="https://fonts.googleapis.com/css2?family=Bebas+Neue&family=Raleway:wght@300&display=swap">
<style>
  :root {
    --backdrop: #333333;
    --paper: #ffffff;
    --accent-red: #990000;
    --ink-dark: #333333;
    --ink-author: #222222;
  }
  * { margin: 0; padding: 0; box-sizing: border-box; }
  html, body {
    width: 1075px;
    height: 1200px;
    overflow: hidden;
    background: var(--backdrop);
  }
  .book-cover {
    position: absolute;
    left: 217px;
    top: 147px;
    width: 641px;
    height: 906px;
    background: var(--paper);
  }
  .accent-bar {
    position: absolute;
    background: var(--accent-red);
  }
  .accent-bar--title { left: 0; top: 86px; width: 28px; height: 109px; }
  .accent-bar--subtitle { right: 0; top: 351px; width: 29px; height: 414px; }
  .headline {
    position: absolute;
    font-family: "Bebas Neue", "Oswald", sans-serif;
    font-weight: 400;
    line-height: 1;
    white-space: nowrap;
  }
  .main-title {
    left: 55px;
    top: 93px;
    font-size: 110px;
    color: var(--accent-red);
  }
  .subtitle-line {
    right: 62px;
    font-size: 77px;
    text-align: right;
  }
  .subtitle-line--red { color: var(--accent-red); }
  .subtitle-line--dark { color: var(--ink-dark); }
  .subtitle-line--small { font-size: 50px; }
  .line-fostering { top: 379px; }
  .line-growth { top: 458px; }
  .line-and { top: 547px; }
  .line-inspiring { top: 608px; }
  .line-excellence { top: 688px; }
  .author {
    position: absolute;
    left: 0;
    width: 641px;
    top: 838px;
    text-align: center;
    font-family: "Raleway", "Helvetica Neue", sans-serif;
    font-weight: 300;
    font-size: 26px;
    color: var(--ink-author);
  }
</style>
</head>
<body>
  <main class="book-cover">
    <div class="accent-bar accent-bar--title"></div>
    <h1 class="headline main-title">Leadership</h1>

    <div class="accent-bar accent-bar--subtitle"></div>
    <p class="headline subtitle-line subtitle-line--red line-fostering">FOSTERING</p>
    <p class="headline subtitle-line subtitle-line--red line-growth">GROWTH</p>
    <p class="headline subtitle-line subtitle-line--dark subtitle-line--small line-and">AND</p>
    <p class="headline subtitle-line subtitle-line--dark line-inspiring">INSPIRING</p>
    <p class="headline subtitle-line subtitle-line--dark line-excellence">EXCELLENCE</p>

    <p class="author">Author: Daniel Ashford</p>
  </main>
</body>
</html>
```